Lumen Ridge Tri-Fold Brochure - Recovering From Alzheimer's

Design a brochure a brochure for Lumen Ridge. www.lumenridge-example.org. We help people with Alzheimer's, or who have had a Traumatic Brain Injury, Concussion or Stroke stop their cognitive decline, and actually reverse decline and improve their cognitive abilities. We use an individualized approach, utilizing extensive lab work and developing a roadmap that includes diet, supplementation, theraputic devices all guided by a Memory Coach. I would like to see a design with pictures of people similar to the demographic on the website. Also incorporate some of the colors from my logo. We offer hope to people who consistently hear, "There is nothing we can do. Alzheimer's is a fatal disease." NOT TRUE! We see people's lives change every day!!!!

Target Market(s)

People who ARE or know someone suffering from cognitive decline, Alzheimer's, Traumatic Brain Injury, Concussion or Stroke.

Industry/Entity Type

Health and wellbeing -- Treating Alzheimer's.

Font styles to use
Other font styles liked:
• Calibri or I think it's called Lota

Colors
0054AA
0677BA
7BADD7
CADEEF
E8F1F8
0094D4
00A9DD
6FCCEA
C7EBF8
E9F6FB
00AB8E
00BBA5
67D7C9
C6EFE9
E9F9F6

Requirements
Must have
• Easily read material (think older eyes) and people between the ages of 40-70. Needs to have a professional feel but not clinical. Create trust and a feeling of caring and hope.
Nice to have
• Please check out my website: www.lumenridge-example.org for content and feel.
Should not have
• Youthful people exercising OR highly stereotypical ageist photos or info.

```html
<!DOCTYPE html>
<html lang="en">
<head>
<meta charset="utf-8">
<title>Lumen Ridge Tri-Fold Brochure</title>
<link rel="stylesheet" href="https://fonts.googleapis.com/css2?family=Montserrat:wght@500;600;700;800&family=Lato:wght@400;700&family=Oswald:wght@500;600&display=swap">
<style>
:root{
  --navy:#0d3a6b;
  --navy-deep:#0a2f58;
  --green:#1fa41f;
  --green-bright:#33c92b;
  --blue:#1b74c9;
  --ink:#1c1c1c;
  --paper:#ffffff;
  --mist:#eef0f2;
  --stage:#e8ede8;
}
*{box-sizing:border-box;margin:0;padding:0}
html,body{width:1200px;height:900px;overflow:hidden;background:var(--stage)}
body{position:relative;font-family:"Lato",sans-serif;color:var(--ink)}
.spread{position:absolute;top:223px;width:585px;height:453px;display:flex;box-shadow:0 6px 20px rgba(0,0,0,.18)}
.spread--outside{left:10px}
.spread--inside{left:605px}
.panel{position:relative;width:195px;height:453px;overflow:hidden}
.photo{position:absolute;left:0;right:0}
.brand{font-family:"Montserrat",sans-serif;font-weight:700;color:var(--blue);letter-spacing:.5px;text-align:center;display:flex;align-items:center;justify-content:center;gap:5px}
.brand__dot{width:9px;height:9px;border-radius:50%;background:var(--green)}
/* outside: intro panel */
.intro{background:var(--paper);padding:14px 12px 0 14px}
.intro__title{font-family:"Montserrat",sans-serif;font-weight:700;font-size:10px;line-height:1.05;color:var(--ink)}
.intro__title span{color:var(--green);display:block}
.intro p{font-size:5.2px;line-height:1.35;margin-top:5px}
.intro .photo{bottom:0;height:150px;background:linear-gradient(160deg,#d9c6b0,#f1e7da 45%,#b9a48d)}
/* contact panel */
.contact{background:linear-gradient(180deg,var(--navy),var(--navy-deep));color:#fff;text-align:center;padding-top:100px}
.contact .brand{font-size:12px;color:#2f9ee6}
.contact__title{font-family:"Montserrat",sans-serif;font-weight:700;font-size:17px;margin-top:26px}
.contact__title span{color:var(--green-bright)}
.contact__rule{width:118px;height:1px;background:#9bb3cf;margin:5px auto 0;position:relative}
.contact__rule::after{content:"";position:absolute;left:50%;top:-1px;width:22px;height:3px;margin-left:-11px;background:var(--green-bright)}
.contact__name{font-family:"Montserrat",sans-serif;font-weight:500;font-size:9px;color:var(--green-bright);margin-top:24px}
.contact__icons{width:100px;height:14px;border:1px solid #cfd9e6;border-radius:2px;margin:6px auto 0;display:flex;justify-content:space-around;align-items:center}
.contact__line{font-family:"Montserrat",sans-serif;font-weight:600;font-size:8px;margin-top:14px;letter-spacing:.3px}
.contact__social{display:flex;justify-content:center;gap:16px;margin-top:20px}
.contact__social i{width:9px;height:9px;border-radius:50%;background:#fff;display:block}
/* cover */
.cover{background:var(--mist)}
.cover .brand{position:absolute;top:58px;left:0;right:0;font-size:11px}
.cover .photo{top:84px;height:236px;background:linear-gradient(180deg,#c7cdc5,#8f9a86 55%,#6b7466)}
.cover__wave{position:absolute;left:0;top:295px;width:195px}
.cover__band{position:absolute;left:0;right:0;top:318px;bottom:0;background:linear-gradient(180deg,var(--green-bright),var(--green));text-align:center;color:#fff}
.cover__name{font-family:"Oswald",sans-serif;font-weight:600;font-size:32px;line-height:1;margin-top:6px;letter-spacing:-.3px}
.cover__help{font-family:"Montserrat",sans-serif;font-weight:800;font-size:15px;color:var(--navy);line-height:1;margin-top:2px}
.cover__rule{width:38px;height:1.5px;background:#fff;margin:4px auto 0}
.cover__tag{font-family:"Montserrat",sans-serif;font-weight:600;font-size:8px;line-height:1.15;margin-top:6px}
.cover__url{font-size:7px;margin-top:5px}
/* inside: services */
.services{background:linear-gradient(180deg,var(--navy),var(--navy-deep));color:#fff;padding:14px 0 0 14px}
.services__title{font-family:"Montserrat",sans-serif;font-weight:700;font-size:10px}
.services__title span{color:var(--green-bright)}
.services__sub{font-family:"Montserrat",sans-serif;font-weight:600;font-size:9px;margin-top:12px;padding-bottom:3px;border-bottom:1px solid #9bb3cf;width:110px}
.service{position:relative;height:78px;margin-top:12px}
.service__photo{position:absolute;left:4px;top:2px;width:56px;height:50px;border-radius:50%;border:2px solid var(--green-bright);background:radial-gradient(circle at 50% 40%,#d8c7b7,#8c7a6c)}
.service__head{position:absolute;left:60px;right:0;top:0;height:10px;background:var(--green-bright);font-family:"Montserrat",sans-serif;font-weight:700;font-size:7.2px;color:var(--navy);padding-left:6px;line-height:10px}
.service__text{position:absolute;left:63px;right:8px;top:12px;font-size:5.2px;line-height:1.3}
.services .photo{bottom:0;height:112px;left:0;width:180px;background:linear-gradient(150deg,#e6dccf,#c9b8a6 60%,#8a7a6d)}
/* professionals */
.pro{background:var(--mist)}
.pro .photo{top:0;height:170px;background:linear-gradient(180deg,#b9b2a8,#d7cbbd 50%,#a89682)}
.pro__wave{position:absolute;left:0;top:150px;width:195px}
.pro__body{position:absolute;top:182px;left:12px;right:10px}
.pro__title{font-family:"Montserrat",sans-serif;font-weight:600;font-size:8.6px;padding-bottom:3px;border-bottom:1px solid #8fb0d6;position:relative}
.pro__title::after{content:"";position:absolute;left:18px;bottom:-1.5px;width:18px;height:3px;background:var(--green)}
.pro__lead{font-family:"Montserrat",sans-serif;font-weight:600;font-size:7.6px;color:var(--navy);margin-top:9px;line-height:1.2}
.pro__lead span{color:var(--green);display:block}
.pro__list{list-style:none;margin-top:8px}
.pro__list li{display:flex;gap:5px;align-items:flex-start;font-family:"Montserrat",sans-serif;font-weight:600;font-size:5.6px;line-height:1.15;margin-bottom:7px;color:#222}
.pro__list svg{flex:none;margin-top:.5px}
/* therapy devices */
.devices{background:var(--paper);padding:16px 12px 0 14px}
.devices__title{font-family:"Montserrat",sans-serif;font-weight:600;font-size:8.6px;padding-bottom:3px;border-bottom:1px solid #8fb0d6;position:relative;width:150px}
.devices__title::after{content:"";position:absolute;left:12px;bottom:-1.5px;width:18px;height:3px;background:var(--green)}
.device{margin-top:11px}
.device__tab{display:flex;align-items:center;gap:5px;width:125px;height:12px;background:linear-gradient(90deg,var(--green),var(--green-bright));clip-path:polygon(0 0,100% 0,97% 100%,0 100%);font-family:"Montserrat",sans-serif;font-weight:700;font-size:6.6px;color:#fff}
.device__icon{width:12px;height:12px;background:var(--navy);display:flex;align-items:center;justify-content:center}
.device p{font-size:5px;line-height:1.3;margin-top:3px}
.devices .photo{bottom:0;height:105px;background:linear-gradient(150deg,#cfd8c0,#d89a6c 45%,#c25a7e 65%,#e2c24c)}
</style>
</head>
<body>

<section class="spread spread--outside" aria-label="Brochure outside">
  <article class="panel intro">
    <h2 class="intro__title">YOUR BRAIN HEALTH <span>HEADQUARTERS</span></h2>
    <p>Lumen Ridge is your brain headquarters. We are a resource you can turn to for the latest tools, therapeutic devices, guidance, programs, and insight necessary to protect and enhance your most important asset: YOUR BRAIN.</p>
    <p>Lumen Ridge has partnered with Cedar Path Partners located in Fairhaven, Idaho. All labs are reviewed, and the Renew Protocol is collaboratively developed and reviewed by Cedar Path Partners. Their expertise and ongoing research bring another layer of assurance and confidence to the process.</p>
    <p>According to the National Memory Council, there are currently 6.2 million Americans living with Alzheimer's disease. That number is on target to triple between 2050 and 2060.</p>
    <p>By the time a person reaches 65 years of age, 2 out of 9 have Alzheimer's. In fact, latest research indicates that well over 10 years before the first symptoms appear (as Mild Cognitive Impairment) the disease is already at work in the brain. By the time a person reaches 85 over 32% will have Alzheimer's and that number is increasing.</p>
    <p>Present medications only manage symptoms or reduce existing Amyloid Plaque. New medications can cost as much as $52,000 a year, must be administered by IV and require monitoring through brain scans.</p>
    <p>The prevailing understanding has been that there is no cure, and Alzheimer's takes no hostages. All die!</p>
    <div class="photo" role="img" aria-label="Photo of a smiling older couple embracing"></div>
  </article>

  <article class="panel contact">
    <div class="brand"><span class="brand__dot"></span>LUMEN RIDGE</div>
    <h2 class="contact__title">Contact <span>Us</span></h2>
    <div class="contact__rule"></div>
    <div class="contact__name">LUMEN RIDGE</div>
    <div class="contact__icons">
      <svg width="7" height="8" viewBox="0 0 10 12" aria-label="Location"><path d="M5 11C2 7 1.5 5.5 1.5 4.5a3.5 3.5 0 017 0C8.5 5.5 8 7 5 11z" fill="none" stroke="#3cd23a" stroke-width="1.2"/><circle cx="5" cy="4.5" r="1.2" fill="#3cd23a"/></svg>
      <svg width="8" height="8" viewBox="0 0 12 12" aria-label="Phone"><path d="M2 1.5l2.2-.3 1.2 2.6-1.4 1a6 6 0 003 3l1-1.4 2.6 1.2-.3 2.2C6 10 2 6 2 1.5z" fill="none" stroke="#3cd23a" stroke-width="1.1"/></svg>
      <svg width="9" height="7" viewBox="0 0 12 9" aria-label="Email"><rect x=".6" y=".6" width="10.8" height="7.8" fill="none" stroke="#3cd23a" stroke-width="1.1"/><path d="M.6.6L6 5l5.4-4.4" fill="none" stroke="#3cd23a" stroke-width="1.1"/></svg>
      <svg width="8" height="8" viewBox="0 0 12 12" aria-label="Website"><circle cx="6" cy="6" r="5" fill="none" stroke="#3cd23a" stroke-width="1.1"/><path d="M1 6h10M6 1c-2.5 3-2.5 7 0 10M6 1c2.5 3 2.5 7 0 10" fill="none" stroke="#3cd23a" stroke-width="1"/></svg>
    </div>
    <div class="contact__line">Somewhere Northfield, ND</div>
    <div class="contact__line">555-010-4242</div>
    <div class="contact__line">info@lumenridge-example.org</div>
    <div class="contact__line">www.lumenridge-example.org</div>
    <div class="contact__social" aria-label="Social media"><i></i><i></i><i></i><i></i></div>
  </article>

  <article class="panel cover">
    <div class="brand"><span class="brand__dot"></span>LUMEN RIDGE</div>
    <div class="photo" role="img" aria-label="Photo of an older couple walking outdoors together"></div>
    <svg class="cover__wave" viewBox="0 0 195 30" height="30" aria-hidden="true">
      <path d="M0 14C60 0 130 0 195 6V30H0z" fill="var(--blue)"/>
      <path d="M0 20C60 6 130 6 195 12V30H0z" fill="var(--green-bright)"/>
    </svg>
    <div class="cover__band">
      <div class="cover__name">LUMEN RIDGE</div>
      <div class="cover__help">IS HERE TO HELP</div>
      <div class="cover__rule"></div>
      <div class="cover__tag">TAKING CARE OF YOUR BRAIN<br>SHOULD NOT BE A MYSTERY</div>
      <div class="cover__url">www.lumenridge-example.org</div>
    </div>
  </article>
</section>

<section class="spread spread--inside" aria-label="Brochure inside">
  <article class="panel services">
    <h2 class="services__title"><span>OUR</span> SERVICES</h2>
    <h3 class="services__sub">Personal Services</h3>
    <div class="service">
      <div class="service__photo" role="img" aria-label="Portrait photo of an older woman"></div>
      <div class="service__head">Individualized Protocol</div>
      <p class="service__text">Based on your personal health history and labwork, a custom Pathway Plan will be generated just for you. When combined with individual coaching and therapy devices it will help you truly optimize your brain health.</p>
    </div>
    <div class="service">
      <div class="service__photo" role="img" aria-label="Photo of an older couple at home"></div>
      <div class="service__head">Customized Support</div>
      <p class="service__text">Whatever your need, be it education on how to help a loved one with dementia, or finding answers to your own cognitive concerns, Lumen Ridge is your compassionate resource to aide you in achieving your goals.</p>
    </div>
    <div class="service">
      <div class="service__photo" role="img" aria-label="Photo of hands holding in support"></div>
      <div class="service__head">Personal Coaching</div>
      <p class="service__text">Our coaches will aide you implement the personalized recommendations of your Renew Protocol Pathway Plan, track your success, coordinate any special needs you may have, problem solve and provide resources.</p>
    </div>
    <div class="photo" role="img" aria-label="Photo of an older woman smiling while using a phone"></div>
  </article>

  <article class="panel pro">
    <div class="photo" role="img" aria-label="Photo of a group of older friends looking at a phone together"></div>
    <svg class="pro__wave" viewBox="0 0 195 24" height="24" aria-hidden="true">
      <path d="M0 14C60 2 130 2 195 12V24H0z" fill="var(--blue)"/>
      <path d="M0 18C60 6 130 6 195 16V24H0z" fill="var(--mist)"/>
    </svg>
    <div class="pro__body">
      <h3 class="pro__title">Services for Professionals</h3>
      <p class="pro__lead">The Renew Protocol in <span>the Workplace:</span></p>
      <ul class="pro__list">
        <li><svg width="7" height="7" viewBox="0 0 10 10"><circle cx="5" cy="5" r="5" fill="var(--green)"/><path d="M2.8 5.2l1.5 1.5 3-3" fill="none" stroke="#fff" stroke-width="1.3"/></svg>Cognitive Assessments</li>
        <li><svg width="7" height="7" viewBox="0 0 10 10"><circle cx="5" cy="5" r="5" fill="var(--green)"/><path d="M2.8 5.2l1.5 1.5 3-3" fill="none" stroke="#fff" stroke-width="1.3"/></svg>The Renew Protocol Lab Panel</li>
        <li><svg width="7" height="7" viewBox="0 0 10 10"><circle cx="5" cy="5" r="5" fill="var(--green)"/><path d="M2.8 5.2l1.5 1.5 3-3" fill="none" stroke="#fff" stroke-width="1.3"/></svg>Comprehensive Health History Review and Integrative Medication Analysis</li>
        <li><svg width="7" height="7" viewBox="0 0 10 10"><circle cx="5" cy="5" r="5" fill="var(--green)"/><path d="M2.8 5.2l1.5 1.5 3-3" fill="none" stroke="#fff" stroke-width="1.3"/></svg>Extensive Bloodwork Analysis</li>
        <li><svg width="7" height="7" viewBox="0 0 10 10"><circle cx="5" cy="5" r="5" fill="var(--green)"/><path d="M2.8 5.2l1.5 1.5 3-3" fill="none" stroke="#fff" stroke-width="1.3"/></svg>Pathway Plan</li>
        <li><svg width="7" height="7" viewBox="0 0 10 10"><circle cx="5" cy="5" r="5" fill="var(--green)"/><path d="M2.8 5.2l1.5 1.5 3-3" fill="none" stroke="#fff" stroke-width="1.3"/></svg>Two One-hour Private Coaching Sessions</li>
        <li><svg width="7" height="7" viewBox="0 0 10 10"><circle cx="5" cy="5" r="5" fill="var(--green)"/><path d="M2.8 5.2l1.5 1.5 3-3" fill="none" stroke="#fff" stroke-width="1.3"/></svg>Access to The Renew Protocol Library of Resources</li>
        <li><svg width="7" height="7" viewBox="0 0 10 10"><circle cx="5" cy="5" r="5" fill="var(--green)"/><path d="M2.8 5.2l1.5 1.5 3-3" fill="none" stroke="#fff" stroke-width="1.3"/></svg>Group Coaching Sessions</li>
        <li><svg width="7" height="7" viewBox="0 0 10 10"><circle cx="5" cy="5" r="5" fill="var(--green)"/><path d="M2.8 5.2l1.5 1.5 3-3" fill="none" stroke="#fff" stroke-width="1.3"/></svg>Use of therapy devices</li>
        <li><svg width="7" height="7" viewBox="0 0 10 10"><circle cx="5" cy="5" r="5" fill="var(--green)"/><path d="M2.8 5.2l1.5 1.5 3-3" fill="none" stroke="#fff" stroke-width="1.3"/></svg>Additional Private Coaching, if Desired</li>
      </ul>
    </div>
  </article>

  <article class="panel devices">
    <h3 class="devices__title">Our Therapy Devices</h3>
    <div class="device">
      <div class="device__tab"><span class="device__icon"><svg width="7" height="7" viewBox="0 0 10 10"><circle cx="5" cy="5" r="2.2" fill="#fff"/><path d="M5 0v1.8M5 8.2V10M0 5h1.8M8.2 5H10" stroke="#fff" stroke-width="1"/></svg></span>RED LIGHT THERAPY</div>
      <p>When you apply a Red Light Therapy device on the head, precise red and near-infrared wavelengths of light travel through the skull and are being absorbed in the brain. This helps damaged brain cells or tissue affected by events such as stroke to replenish and heal.</p>
    </div>
    <div class="device">
      <div class="device__tab"><span class="device__icon"><svg width="7" height="7" viewBox="0 0 10 10"><rect x="1" y="2" width="8" height="7" fill="none" stroke="#fff" stroke-width="1"/><path d="M3 5h4" stroke="#fff" stroke-width="1"/></svg></span>INFRARED SAUNA</div>
      <p>Infrared Saunas have many great health benefits, including expelling of toxins, improving blood circulation, killing disease-causing microbes and improving mitochondrial function.</p>
    </div>
    <div class="device">
      <div class="device__tab"><span class="device__icon"><svg width="7" height="7" viewBox="0 0 10 10"><circle cx="5" cy="4" r="3" fill="none" stroke="#fff" stroke-width="1"/><path d="M2 9h6" stroke="#fff" stroke-width="1"/></svg></span>AVE</div>
      <p>Audio-Visual Entrainment (AVE) is a technique that uses pulses of light and sound at specific frequencies to gently and safely guide the brain into various brainwave patterns. By altering your brainwave frequencies, you can boost your mood, improve sleep patterns, sharpen your mind, and increase relaxation levels.</p>
    </div>
    <div class="device">
      <div class="device__tab"><span class="device__icon"><svg width="7" height="7" viewBox="0 0 10 10"><circle cx="5" cy="5" r="3.5" fill="none" stroke="#fff" stroke-width="1"/><circle cx="5" cy="5" r="1.2" fill="#fff"/></svg></span>PEMF</div>
      <p>PEMF works by stimulating both tissue regeneration and brain signaling and reducing inflammation in the body and brain.</p>
    </div>
    <div class="device">
      <div class="device__tab"><span class="device__icon"><svg width="8" height="6" viewBox="0 0 12 8"><path d="M1 4C3 1 9 1 11 4 9 7 3 7 1 4z" fill="none" stroke="#fff" stroke-width="1"/><circle cx="6" cy="4" r="1.4" fill="#fff"/></svg></span>CLEARSIGHT</div>
      <p>The ClearSight Vision System focuses on functional vision. This is different than your ability to see. Functional vision is how your eyes and brain work together to navigate the world.</p>
    </div>
    <div class="photo" role="img" aria-label="Photo of three older women laughing together outdoors"></div>
  </article>
</section>

</body>
</html>
```